Business Cards used to invite people to our church

We are a church and have need of a business card sized advertisement that allows our members to hand them out in order to invite people to the church. I need the front of the card to say "You're Invited" or "Come Check us out". with the service times on the back of the card later.
I have attached one of the OLD cards we have used in the past, but we want a complete makeover, into a more modern style that does not require the image.
I am also replacing the old logo with a newer "flat" logo which is attached.
Please use marketing colors. (blue or red or something that catches attention)
Create a card that DOES NOT have the picture of the two people on the front
The information on the sample card back is correct to go onto new card
Target Market(s)
anyone
Industry/Entity Type
Business
Contact Information for Business Card
sertice times and address information which you can get from the sample card I uploaded. It should have "You're Invited" or "Come Check us out" on the front of the card with out logo.

```html
<!DOCTYPE html>
<html lang="en">
<head>
<meta charset="utf-8">
<title>Grace Harbor Ministries – Invitation Card</title>
<link href="https://fonts.googleapis.com/css2?family=Open+Sans:wght@400;700&family=Pinyon+Script&display=swap" rel="stylesheet">
<style>
  :root {
    --card-blue: #0a93f0;
    --ink-white: #ffffff;
    --ink-black: #0d0d0d;
    --page-bg: #e9ebee;
    --card-shadow: rgba(0, 0, 0, 0.18);
  }
  * { box-sizing: border-box; margin: 0; padding: 0; }
  html, body { width: 1200px; height: 900px; overflow: hidden; }
  body {
    background: var(--page-bg);
    font-family: "Open Sans", Arial, sans-serif;
    display: flex;
    flex-direction: column;
    align-items: center;
    justify-content: center;
    gap: 56px;
  }
  .card {
    position: relative;
    width: 600px;
    height: 343px;
    background: var(--card-blue);
    box-shadow: 0 8px 24px var(--card-shadow);
    overflow: hidden;
    color: var(--ink-white);
  }

  /* Back: ministry info and schedule */
  .card-back .brand {
    position: absolute;
    top: 46px;
    left: 230px;
    display: flex;
    align-items: center;
    gap: 10px;
  }
  .brand-dot {
    width: 26px; height: 26px;
    border-radius: 50%;
    background: var(--ink-white);
  }
  .brand-name {
    font-weight: 700;
    font-size: 22px;
    letter-spacing: 0.5px;
  }
  .contact {
    position: absolute;
    top: 100px;
    left: 215px;
    font-weight: 700;
    font-size: 14px;
    line-height: 1.6;
  }
  .contact .phone { padding-left: 60px; }
  .schedule {
    position: absolute;
    top: 155px;
    left: 190px;
    width: 330px;
    list-style: none;
    font-size: 14px;
    line-height: 1.75;
  }
  .schedule li { display: flex; align-items: baseline; }
  .schedule .leader {
    flex: 1;
    border-bottom: 2px dotted var(--ink-white);
    margin: 0 3px;
    transform: translateY(-4px);
  }

  /* Front: invitation */
  .invite-title {
    position: absolute;
    top: 92px;
    left: 0; right: 0;
    text-align: center;
    font-family: "Pinyon Script", cursive;
    font-size: 74px;
    color: var(--ink-black);
    -webkit-text-stroke: 1px var(--ink-white);
    text-shadow: 0 0 1px var(--ink-white);
  }
  .front-bands { position: absolute; inset: 0; }
</style>
</head>
<body>

  <section class="card card-back" aria-label="Card back">
    <div class="brand">
      <span class="brand-dot"></span>
      <span class="brand-name">Grace Harbor Ministries</span>
    </div>
    <address class="contact">
      <div>2470 Orchard Lane - Fairview, Tx 75069</div>
      <div class="phone">1-800-555-0192</div>
    </address>
    <ul class="schedule">
      <li><span>Sunday</span><span class="leader"></span><span>9:00 Am</span></li>
      <li><span>Sunday</span><span class="leader"></span><span>11:00 Am</span></li>
      <li><span>Wed. Bible Class</span><span class="leader"></span><span>7:00 Pm</span></li>
    </ul>
  </section>

  <section class="card card-front" aria-label="Card front">
    <svg class="front-bands" width="600" height="343" viewBox="0 0 600 343" aria-hidden="true">
      <polygon points="0,246 300,246 316,270 0,270" fill="var(--ink-black)"/>
      <polygon points="300,270 600,270 600,343 348,343" fill="var(--ink-white)"/>
      <polygon points="300,246 316,270 300,270 292,258" fill="var(--card-blue)"/>
    </svg>
    <h1 class="invite-title">You're Invited</h1>
  </section>

</body>
</html>
```